Packaging design for Prenatal, Fish Oil, and Joint Pain product

We are looking for package design (label and outer box) for following products:
1) Morevia
- Product name: Morevia
- Benefit: Prenatal
- Feature DHA + Folic Acid
- What we need from you? We need box concept
- Box dimension 55mm Height x 145mm length x 100mm width
2) Omega 3 Alaskan Salmon
- Product name: Omega 3 Alaskan Salmon
- Benefit: Cognitive , cardiovascular Health, Joint Health, High cholesterol
- Feature: Alaskan Salmon
- What we need from you? We need label concept
- Label dimension: 60mm Height x 180mm Length
2) Quorby
- Product name: Quorby
- Benefit: Joint Health
- Feature: Glucosamin, Chondroitin, MSM
Designer can use generic text on other vitamin products for formula, usage instruction etc.
We have logo. The logo must be integrated in the packaging design. (please see attachment)
Health

```html
<!DOCTYPE html>
<html lang="en">
<head>
<meta charset="utf-8">
<title>Morevia Women's Prenatal plus DHA – Box Front</title>
<link rel="stylesheet" href="https://fonts.googleapis.com/css2?family=Archivo+Black&family=Lato:ital,wght@0,700;1,400;1,700;1,900&family=Lobster&family=Open+Sans:ital,wght@1,700&display=swap">
<style>
  :root {
    --plum-deep: #5a1340;
    --plum: #7d2460;
    --plum-light: #b4568f;
    --pink: #e0157f;
    --pink-soft: #f4c6de;
    --blush: #fbeaf3;
    --white: #ffffff;
    --ink: #4a1036;
    --ribbon: #ffe94a;
    --ribbon-text: #f07a73;
  }
  html, body {
    margin: 0;
    padding: 0;
    width: 1200px;
    height: 826px;
    overflow: hidden;
    background: var(--white);
  }
  .box-front {
    position: relative;
    width: 1200px;
    height: 826px;
    overflow: hidden;
    background: var(--white);
    font-family: "Lato", sans-serif;
  }
  .box-art {
    position: absolute;
    inset: 0;
  }
  .brand-mark {
    position: absolute;
    left: 250px;
    top: 108px;
    display: flex;
    align-items: center;
    gap: 12px;
    font-family: "Lato", sans-serif;
    font-weight: 700;
    font-size: 62px;
    color: var(--pink-soft);
    letter-spacing: 1px;
  }
  .brand-mark .dot {
    width: 22px;
    height: 22px;
    border-radius: 50%;
    background: var(--pink-soft);
  }
  .product-name {
    position: absolute;
    left: 108px;
    top: 186px;
    margin: 0;
    font-family: "Archivo Black", sans-serif;
    font-size: 190px;
    line-height: 1;
    letter-spacing: -6px;
    color: var(--white);
    -webkit-text-stroke: 5px var(--plum);
    paint-order: stroke fill;
  }
  .product-line {
    position: absolute;
    left: 118px;
    top: 356px;
    margin: 0;
    font-family: "Lato", sans-serif;
    font-style: italic;
    font-weight: 400;
    font-size: 47px;
    color: var(--plum-deep);
  }
  .product-line strong { font-weight: 900; }
  .benefits {
    position: absolute;
    left: 150px;
    top: 432px;
    width: 480px;
    margin: 0;
    padding: 0;
    list-style: none;
    font-style: italic;
    font-size: 20.5px;
    line-height: 31px;
    color: var(--pink);
    text-align: center;
  }
  .benefits li { margin-bottom: 28px; }
  .benefits li::before { content: "• "; }
  .benefits .folic { margin-left: 60px; text-align: left; padding-left: 60px; }
  .benefits .usage { padding-left: 200px; }
  .tablet-callout {
    position: absolute;
    left: 30px;
    top: 628px;
    width: 250px;
    font-style: italic;
    font-size: 20px;
    line-height: 25px;
    color: var(--ink);
    text-align: center;
  }
  .count-bar {
    position: absolute;
    left: 58px;
    top: 752px;
    margin: 0;
    font-family: "Open Sans", sans-serif;
    font-style: italic;
    font-weight: 700;
    font-size: 25px;
    color: var(--white);
  }
  .ribbon-label {
    position: absolute;
    left: 1010px;
    top: 70px;
    font-family: "Lobster", cursive;
    font-size: 92px;
    color: var(--ribbon-text);
    transform: rotate(45deg);
    transform-origin: center;
  }
</style>
</head>
<body>
<main class="box-front">
  <svg class="box-art" width="1200" height="826" viewBox="0 0 1200 826" aria-hidden="true">
    <defs>
      <radialGradient id="header-glow" cx="0.4" cy="0.35" r="0.75">
        <stop offset="0" stop-color="#ffffff"/>
        <stop offset="0.15" stop-color="#f3c9e1"/>
        <stop offset="0.5" stop-color="#a3417f"/>
        <stop offset="1" stop-color="#5d1444"/>
      </radialGradient>
      <linearGradient id="photo-tone" x1="0" y1="0" x2="1" y2="1">
        <stop offset="0" stop-color="#fbe7f1"/>
        <stop offset="0.5" stop-color="#e7b8cf"/>
        <stop offset="1" stop-color="#c98aae"/>
      </linearGradient>
      <radialGradient id="callout-fill" cx="0.35" cy="0.3" r="0.8">
        <stop offset="0" stop-color="#ff8fc6"/>
        <stop offset="0.6" stop-color="#e0157f"/>
        <stop offset="1" stop-color="#b50c63"/>
      </radialGradient>
      <linearGradient id="bar-fill" x1="0" y1="0" x2="0" y2="1">
        <stop offset="0" stop-color="#7a1f58"/>
        <stop offset="1" stop-color="#4f0f37"/>
      </linearGradient>
    </defs>

    <path class="header-panel" d="M20 20 H1180 V350 H20 Z" fill="url(#header-glow)"/>
    <path class="content-panel" d="M20 352 H880 L760 735 H20 Z" fill="#ffffff"/>

    <path class="photo-swoosh" d="M870 20 C760 160 700 420 745 735 H790 C760 470 800 220 910 20 Z" fill="#6a1a4f"/>
    <path class="photo-swoosh-light" d="M905 20 C800 210 770 450 790 735 H812 C790 470 830 230 930 20 Z" fill="#c16ea0"/>
    <g role="img" aria-label="Photo of a smiling expectant mother resting against pillows, holding her belly">
      <path d="M930 20 H1180 V735 H812 C792 470 830 230 930 20 Z" fill="url(#photo-tone)"/>
    </g>

    <polygon class="new-ribbon" points="870,20 1010,20 1180,190 1180,330" fill="var(--ribbon)"/>

    <g role="img" aria-label="Illustration of one multivitamin tablet and one DHA softgel">
      <circle cx="135" cy="676" r="97" fill="url(#callout-fill)"/>
      <ellipse cx="120" cy="630" rx="70" ry="35" fill="#ffffff" opacity="0.18"/>
    </g>

    <rect class="count-bar-band" x="20" y="735" width="1160" height="70" fill="url(#bar-fill)"/>
    <rect x="20" y="735" width="1160" height="3" fill="var(--pink)"/>
    <rect x="20" y="20" width="1160" height="785" fill="none" stroke="#ffffff" stroke-width="2"/>
  </svg>

  <div class="brand-mark"><span class="dot"></span>Veloa</div>

  <h1 class="product-name">Morevia</h1>
  <p class="product-line">Women’s Prenatal plus <strong>DHA</strong></p>

  <ul class="benefits">
    <li>DHA to support healthy fetal brain and eye development during pregnancy* and is also recommended by doctors while breastfeeding</li>
    <li class="folic">100% of recommended Folic Acid</li>
    <li class="usage">For Use Before, During and After Pregnancy</li>
  </ul>

  <p class="tablet-callout">An illustration<br>of a each tablet and Softgel<br>in here</p>

  <div class="ribbon-label">new</div>

  <p class="count-bar">70 Prenatal Multivitamin/Mineral Tablets &amp; 70 Prenatal DHA/EPA Softgels</p>
</main>
</body>
</html>
```